Diverse, up-scale salon needs eye-catching, unique business cards.

We are looking for a unique business card design for our stylist but that can also be multi functional and used for appointment reminder and referrals. I will need a design in a format that I can modify names and titles going forward. In the past we have had a dark background with the logo on one side, and stylist and contact information on the other but we are open to all ideas. I have included our mission statement as well as branded colors below. The statement doesn't need to go on the card, it's just a reference for target market. We need space for the stylists name, title, instagram handle and then the salons phone number, website and address. I am also open to adding a spot for a qr code linked to the stylist instagram or the salon booking link.

primary brand colors:
#333333 #233415 #36502a #93874a #000000
Mission statement:
Vessolin Hair Studio, a high-end salon located in the lively Downtown Farmington, Michigan, is committed to providing exceptional services in a welcoming and relaxed environment to meet the needs of our diverse clientele.
Our salon specializes in contemporary custom haircuts, coloring, extensions, and barbering and beard grooming services. Our team of skilled stylists is passionate and inventive in their hair styling techniques. At the heart of our salon are values centered on quality, innovation, creativity, and above all, comfort. These core values are evident in every appointment across our customizable array of services.
Our goal is to establish a benchmark for exceptional hair care for every human.
Website: www.vessolinhairstudio.example
instagram: @vessolinhairstudio
address: 41782 Pelham Crest Rd, Farmington MI
phone: 248-613-4087

Industry/Entity Type

Hair Salon

Contact Information for Business Card

Stylist name, title, phone, instagram, website, address, (optional qr code)

Requirements
Should not have
• Does not need mission statement on the card.

```html
<!DOCTYPE html>
<html lang="en">
<head>
<meta charset="utf-8">
<title>Vessolin Hair Studio – Business Card</title>
<link href="https://fonts.googleapis.com/css2?family=Arimo:wght@400;700&display=swap" rel="stylesheet">
<style>
  :root {
    --gold: #93874a;
    --charcoal: #333333;
    --stage: #1c1c1c;
    --paper: #ffffff;
    --ink-soft: #7a7a7a;
    --ink-light: #ffffff;
  }
  * { margin: 0; padding: 0; box-sizing: border-box; }
  html, body { width: 1200px; height: 1059px; overflow: hidden; background: var(--stage); }
  body { position: relative; font-family: "Arimo", Arial, sans-serif; }

  .card { position: absolute; }
  .card-front { left: 258px; top: 89px; width: 689px; height: 393px; background: var(--paper); }
  .card-back { left: 252px; top: 540px; width: 701px; height: 401px; background: var(--charcoal); }

  .frame { position: absolute; left: 19px; top: 19px; right: 19px; bottom: 19px; border: 2px solid var(--gold); }

  .brand-seal {
    position: absolute; display: flex; align-items: center; justify-content: center;
    border-radius: 50%; border: 3px solid var(--gold);
    color: var(--gold); font-weight: 700; text-align: center; text-transform: uppercase;
    letter-spacing: 2px; line-height: 1.25;
  }
  .card-front .brand-seal { left: 102px; top: 100px; width: 192px; height: 192px; font-size: 17px; }
  .card-back .brand-seal { left: 394px; top: 83px; width: 236px; height: 236px; font-size: 21px; }

  .divider { position: absolute; left: 325px; top: 100px; width: 2px; height: 193px; background: var(--ink-soft); }

  .contact { position: absolute; left: 354px; top: 96px; color: var(--ink-soft); }
  .contact .name { color: var(--gold); font-weight: 700; font-size: 21px; line-height: 24px; }
  .contact .title { font-size: 15px; line-height: 17px; }
  .contact .address { margin-top: 20px; font-size: 19px; line-height: 25px; }
  .contact .lines { margin-top: 10px; list-style: none; }
  .contact .lines li { display: flex; align-items: center; font-size: 19px; line-height: 28.5px; }
  .contact .lines svg { width: 16px; height: 16px; margin-right: 10px; flex: none; }

  .services { position: absolute; left: 43px; top: 52px; }
  .services h2 { color: var(--gold); font-weight: 700; font-size: 21px; line-height: 26px; margin-bottom: 4px; }
  .services ul { list-style: none; }
  .services li { color: var(--ink-light); font-size: 21px; line-height: 26.7px; display: flex; align-items: center; }
  .services li::before { content: ""; width: 9px; height: 9px; border-radius: 50%; background: var(--gold); margin: 0 9px 0 5px; }
</style>
</head>
<body>
  <section class="card card-front">
    <div class="frame"></div>
    <div class="brand-seal">Vessolin<br>Hair Studio</div>
    <div class="divider"></div>
    <div class="contact">
      <div class="name">DANIEL MERCER</div>
      <div class="title">Manager</div>
      <div class="address">41782 Pelham Crest Rd<br>Farmington MI</div>
      <ul class="lines">
        <li>
          <svg viewBox="0 0 24 24" fill="none" stroke="#93874a" stroke-width="2.4"><path d="M5 3h4l2 5-3 2a12 12 0 0 0 6 6l2-3 5 2v4a2 2 0 0 1-2 2A17 17 0 0 1 3 5a2 2 0 0 1 2-2z"/></svg>
          248-613-4087
        </li>
        <li>
          <svg viewBox="0 0 24 24" fill="none" stroke="#93874a" stroke-width="2.6"><rect x="3" y="3" width="18" height="18" rx="5"/><circle cx="12" cy="12" r="4"/></svg>
          @vessolinhairstudio
        </li>
        <li>
          <svg viewBox="0 0 24 24" fill="none" stroke="#93874a" stroke-width="1.8"><circle cx="12" cy="12" r="9"/><ellipse cx="12" cy="12" rx="4" ry="9"/><path d="M3 12h18M5 7h14M5 17h14"/></svg>
          www.vessolinhairstudio.example
        </li>
      </ul>
    </div>
  </section>

  <section class="card card-back">
    <div class="services">
      <h2>OUR SERVICES</h2>
      <ul>
        <li>Custom Haircuts</li>
        <li>Coloring</li>
        <li>Extensions</li>
        <li>And Barbering</li>
        <li>Beard Grooming</li>
      </ul>
    </div>
    <div class="brand-seal">Vessolin<br>Hair Studio</div>
  </section>
</body>
</html>
```